Redesign website for small print company

Vindurgata is a small printing company in Iceland mainly servicing Students, schools, etc. We are also doing all kind of other jobs, like business cards, book printing, brochure printing etc. We are also selling books online.
Our website is: www.vindurgata.is
What we are looking for is:
- Web Design (Uncoded - PSD layout only)
- Mobile friendly design, using our current color scheme: Red, green, yellow and light gray.
- Clean simple design
- Simple, light and easy to use.
- More menu Items/drop down
Industry/Entity Type
Digital Printing
Number of Pages Required
5+ page
Requirements
Must have
- Easy navigation
- Designed for mobile
- Current color scheme (see logo)
Nice to have
- Icon based products

```html
<!DOCTYPE html>
<html lang="is">
<head>
<meta charset="utf-8">
<title>Vindurgata – Prentþjónusta</title>
<link href="https://fonts.googleapis.com/css2?family=Raleway:wght@400;500;600;700;800&family=Montserrat:wght@500;700&display=swap" rel="stylesheet">
<style>
:root{
  --red:#e53935;
  --green:#2e9e48;
  --yellow:#f5c400;
  --blue:#2a6fd6;
  --light:#f3f3f3;
  --ink:#2b2b2b;
  --muted:#8a8a8a;
  --dark:#1e1e1e;
  --darker:#111;
  --white:#fff;
}
*{box-sizing:border-box;margin:0;padding:0}
html,body{width:1200px;height:3420px;overflow:hidden}
body{font-family:"Raleway",sans-serif;color:var(--ink);background:var(--white);position:relative}
.abs{position:absolute}

/* header + hero */
.hero{left:0;top:0;width:1200px;height:640px;
  background:linear-gradient(180deg,#7f8fa0 0%,#c7b59a 30%,#e9c98d 42%,#6c7c86 52%,#3b4a52 70%,#2a2f30 100%)}
.topbar{left:0;top:0;width:1200px;height:60px;background:rgba(0,0,0,.55);display:flex;align-items:center;padding:0 40px;color:var(--white)}
.brand{display:flex;align-items:center;gap:10px;font-weight:800;font-size:22px;letter-spacing:.5px}
.brand-mark{width:22px;height:22px;background:var(--yellow)}
.topbar .sep{width:1px;height:28px;background:rgba(255,255,255,.35);margin:0 24px}
.hours{font-size:15px;font-weight:600;display:flex;align-items:center;gap:8px}
.services{font-size:12px;font-weight:600;letter-spacing:.5px}
.tools{margin-left:auto;display:flex;align-items:center;gap:22px}
.phone{font-size:24px;font-weight:700;display:flex;align-items:center;gap:10px}
.cta-top{left:955px;top:158px;width:150px;height:40px;background:var(--red);color:var(--white);font-weight:700;font-size:15px;letter-spacing:.5px;display:flex;align-items:center;justify-content:center}
.hero-title{left:100px;top:258px;font-family:"Montserrat",sans-serif;font-weight:700;font-size:68px;color:var(--white);text-shadow:0 2px 8px rgba(0,0,0,.35)}
.arrow{top:290px;color:var(--white);font-size:34px;font-weight:700}
.hero-badge{left:1130px;top:522px;width:36px;height:36px;border-radius:50%;background:rgba(255,255,255,.8)}

/* category cards */
.card{top:640px;width:260px;height:360px;background:var(--white);box-shadow:0 4px 14px rgba(0,0,0,.12);text-align:center}
.card .shot{height:180px}
.card .pin{position:absolute;top:-14px;left:122px;width:16px;height:16px;border-radius:50%;box-shadow:0 2px 4px rgba(0,0,0,.35)}
.card .pin::after{content:"";position:absolute;left:7px;top:14px;width:2px;height:14px;background:#999}
.card h3{font-size:20px;font-weight:800;margin-top:24px;letter-spacing:.5px}
.card .more{font-size:12px;font-weight:700;color:var(--muted);margin-top:4px;letter-spacing:1px}
.card p{font-size:13px;line-height:1.7;color:var(--muted);padding:14px 26px 0}

/* about */
.section-title{width:1200px;left:0;text-align:center;font-size:44px;font-weight:700;color:var(--ink)}
.about-text{left:80px;top:1128px;width:560px;font-size:14px;line-height:1.85;color:#555}
.about-text p+p{margin-top:14px}
.btn-red{background:var(--red);color:var(--white);font-weight:700;font-size:14px;letter-spacing:.8px;display:flex;align-items:center;justify-content:center;gap:10px}
.know-more{left:80px;top:1292px;width:140px;height:42px}
.about-box{left:680px;top:1218px;width:320px;height:130px;background:var(--light);box-shadow:0 6px 20px rgba(0,0,0,.15);display:flex;align-items:center;justify-content:center;font-weight:800;font-size:24px;letter-spacing:.5px}

/* action tiles */
.tile{top:1410px;width:320px;height:230px;background:var(--white);box-shadow:0 4px 16px rgba(0,0,0,.1);display:flex;flex-direction:column;align-items:center;justify-content:center;gap:22px}
.tile span{font-size:16px;font-weight:600;letter-spacing:.6px;color:#444}

/* products */
.products{left:0;top:1740px;width:1200px;height:600px;background:linear-gradient(160deg,#2a2a2e 0%,#3c3a3f 40%,#262628 100%);color:var(--white)}
.products .section-title{color:var(--white);top:40px}
.prod{width:340px;text-align:center}
.prod h4{font-size:26px;font-weight:500;margin-top:10px}
.prod p{font-size:12.5px;line-height:1.6;color:#d0d0d0;margin-top:6px}

/* contact */
.contact-photo{left:160px;top:2440px;width:360px;height:340px;background:linear-gradient(170deg,#f2f2f2 0%,#d9c3a8 45%,#8a2b2b 100%)}
.contact-intro{left:600px;top:2440px;width:520px;font-size:13px;line-height:1.7;color:#666}
.field{height:46px;border-bottom:1px solid #ddd;font-size:13px;color:#888;display:flex;align-items:flex-end;padding-bottom:8px;width:250px}
.send{left:600px;top:2680px;width:210px;height:46px}

/* footer */
.map{left:0;top:2780px;width:640px;height:580px;background:linear-gradient(135deg,#eef0ea 0%,#e3e7e0 50%,#f1e7c9 100%)}
.footer{left:640px;top:2780px;width:560px;height:580px;background:var(--dark);color:var(--white);padding:52px 60px}
.footer h5{font-size:18px;font-weight:700;letter-spacing:.6px;margin-bottom:18px}
.footer .line{width:36px;height:2px;background:var(--red);margin:-10px 0 20px}
.footer p,.footer .row{font-size:13px;color:#cfcfcf;line-height:1.7}
.footer .row{display:flex;align-items:center;gap:10px}
.social{width:40px;height:40px;border-radius:50%;border:2px solid #cfcfcf}
.bottom{left:0;top:3360px;width:1200px;height:60px;background:var(--darker);color:#bbb;font-size:13px;display:flex;align-items:center;justify-content:center}
</style>
</head>
<body>

<div class="abs hero" role="img" aria-label="Ljósmynd af strönd við sólarlag"></div>

<header class="abs topbar">
  <div class="brand"><span class="brand-mark"></span>Vindurgata</div>
  <span class="sep"></span>
  <div class="hours">
    <svg width="18" height="18" viewBox="0 0 24 24"><circle cx="12" cy="12" r="10" fill="none" stroke="#fff" stroke-width="2"/><path d="M12 6v6l4 2" stroke="#fff" stroke-width="2" fill="none"/></svg>
    Mán – Fri 9-17
  </div>
  <span class="sep"></span>
  <div class="services">FJÖLÞJÓNUSTA | SALA &amp; VERKUM</div>
  <div class="tools">
    <svg width="20" height="20" viewBox="0 0 24 24"><circle cx="10" cy="10" r="7" fill="none" stroke="#fff" stroke-width="2.4"/><path d="M15 15l6 6" stroke="#fff" stroke-width="2.4"/></svg>
    <svg width="22" height="22" viewBox="0 0 24 24"><path d="M6 7h12l-1 13H7z" fill="none" stroke="#fff" stroke-width="2"/><path d="M9 7a3 3 0 016 0" fill="none" stroke="#fff" stroke-width="2"/></svg>
    <span class="sep" style="margin:0"></span>
    <div class="phone">
      <svg width="22" height="22" viewBox="0 0 24 24"><path d="M6 2l4 4-2 3a12 12 0 007 7l3-2 4 4-3 4C10 22 2 14 2 5z" fill="#fff"/></svg>
      555 0142
    </div>
  </div>
</header>

<div class="abs btn-red cta-top">HAFA SAMBAND</div>
<h1 class="abs hero-title">Þetta reddast !</h1>
<div class="abs arrow" style="left:22px">‹</div>
<div class="abs arrow" style="left:1162px">›</div>
<div class="abs hero-badge"></div>

<!-- categories -->
<article class="abs card" style="left:80px">
  <div class="shot" role="img" aria-label="Mynd af prentuðum bókum" style="background:linear-gradient(135deg,#e8d8c4,#c85a4a 60%,#5a7ab0)"></div>
  <span class="pin" style="background:var(--red)"></span>
  <h3>BÆKUR</h3><div class="more">NÁNAR</div>
  <p>Vindurgata prentar bækur fyrir nemendur, skóla og höfunda af öllum stærðum.</p>
</article>
<article class="abs card" style="left:470px">
  <div class="shot" role="img" aria-label="Mynd af nafnspjöldum" style="background:linear-gradient(135deg,#dcdcdc,#f4f4f4 55%,#c44)"></div>
  <span class="pin" style="background:var(--yellow)"></span>
  <h3>NAFNSPJÖLD</h3><div class="more">NÁNAR</div>
  <p>Vönduð nafnspjöld prentuð hratt á góðan pappír fyrir fyrirtæki og einstaklinga.</p>
</article>
<article class="abs card" style="left:860px">
  <div class="shot" role="img" aria-label="Mynd af innbundnum ritgerðum" style="background:linear-gradient(135deg,#f1f1f1,#d8d8d8 60%,#8aa)"></div>
  <span class="pin" style="background:var(--green)"></span>
  <h3>RITGERÐIR</h3><div class="more">NÁNAR</div>
  <p>Prentun og innbinding lokaritgerða með stuttum fyrirvara fyrir alla nemendur.</p>
</article>

<!-- about -->
<h2 class="abs section-title" style="top:1050px">About us</h2>
<div class="abs about-text">
  <p>Vindurgata er lítil prentsmiðja í Reykjavík sem þjónar nemendum, skólum og fyrirtækjum. Við prentum ritgerðir, bækur, bæklinga og nafnspjöld með skjótum og persónulegum hætti.</p>
  <p>Við leggjum áherslu á gæði, sanngjarnt verð og góða þjónustu. Sendu okkur verkið þitt á netinu, fáðu tilboð eða láttu okkur hanna fyrir þig frá grunni.</p>
</div>
<div class="abs btn-red know-more">KNOW MORE</div>
<div class="abs about-box">Vindurgata</div>

<!-- tiles -->
<div class="abs tile" style="left:80px">
  <svg width="64" height="56" viewBox="0 0 64 56"><rect x="4" y="14" width="56" height="38" rx="4" fill="var(--green)"/><path d="M22 14V8a4 4 0 014-4h12a4 4 0 014 4v6" fill="none" stroke="var(--green)" stroke-width="4"/><rect x="28" y="28" width="8" height="8" fill="#fff"/></svg>
  <span>SENDA VERK</span>
</div>
<div class="abs tile" style="left:440px">
  <svg width="64" height="64" viewBox="-32 -32 64 64">
    <path d="M0 0L0-30A30 30 0 0121.2-21.2z" fill="#e53935"/>
    <path d="M0 0L21.2-21.2A30 30 0 0130 0z" fill="#fb8c00"/>
    <path d="M0 0L30 0A30 30 0 0121.2 21.2z" fill="#f5c400"/>
    <path d="M0 0L21.2 21.2A30 30 0 010 30z" fill="#7cb342"/>
    <path d="M0 0L0 30A30 30 0 01-21.2 21.2z" fill="#2e9e48"/>
    <path d="M0 0L-21.2 21.2A30 30 0 01-30 0z" fill="#1e88e5"/>
    <path d="M0 0L-30 0A30 30 0 01-21.2-21.2z" fill="#5e35b1"/>
    <path d="M0 0L-21.2-21.2A30 30 0 010-30z" fill="#d81b60"/>
    <circle r="9" fill="#fff"/>
  </svg>
  <span>HANNA VERK</span>
</div>
<div class="abs tile" style="left:800px">
  <svg width="48" height="64" viewBox="0 0 48 64"><path d="M8 18a16 16 0 1132 0c0 10-12 12-12 24" fill="none" stroke="var(--blue)" stroke-width="8" stroke-linecap="round"/><circle cx="28" cy="56" r="5" fill="var(--blue)"/></svg>
  <span>FÁ TILBOÐ</span>
</div>

<!-- products -->
<section class="abs products" role="img" aria-label="Dökk ljósmynd af prentvél í bakgrunni">
  <h2 class="abs section-title">Product List</h2>
  <div class="abs prod" style="left:60px;top:140px">
    <svg width="40" height="44" viewBox="0 0 40 44"><rect x="6" y="2" width="28" height="40" fill="none" stroke="#fff" stroke-width="2.5"/><path d="M12 12h16M12 19h16M12 26h16M12 33h10" stroke="#fff" stroke-width="2"/></svg>
    <h4>Essays</h4><p>Prentun og innbinding ritgerða á vandaðan pappír, tilbúið samdægurs fyrir skil.</p>
  </div>
  <div class="abs prod" style="left:430px;top:140px">
    <svg width="48" height="44" viewBox="0 0 48 44"><rect x="2" y="8" width="44" height="28" rx="2" fill="none" stroke="#fff" stroke-width="2.5"/><circle cx="14" cy="20" r="5" fill="none" stroke="#fff" stroke-width="2"/><path d="M24 18h16M24 25h12" stroke="#fff" stroke-width="2"/></svg>
    <h4>Business cards</h4><p>Nafnspjöld í mörgum útfærslum með mattri eða glansandi áferð á góðu verði.</p>
  </div>
  <div class="abs prod" style="left:800px;top:140px">
    <svg width="44" height="44" viewBox="0 0 44 44"><path d="M4 6l12-3 12 3 12-3v35l-12 3-12-3-12 3z" fill="none" stroke="#fff" stroke-width="2.5"/><path d="M16 3v35M28 6v35" stroke="#fff" stroke-width="2"/></svg>
    <h4>Leaflets</h4><p>Bæklingar og dreifiblöð í litum, brotin eftir þínum þörfum og óskum.</p>
  </div>
  <div class="abs prod" style="left:60px;top:330px">
    <svg width="48" height="44" viewBox="0 0 48 44"><path d="M4 8c8-4 14-4 20 2 6-6 12-6 20-2v30c-8-4-14-4-20 2-6-6-12-6-20-2z" fill="none" stroke="#fff" stroke-width="2.5"/><path d="M24 10v30" stroke="#fff" stroke-width="2"/></svg>
    <h4>Bookprinting</h4><p>Bókaprentun í litlu og stóru upplagi með kápu og innbindingu að eigin vali.</p>
  </div>
  <div class="abs prod" style="left:430px;top:330px">
    <svg width="40" height="44" viewBox="0 0 40 44"><rect x="4" y="4" width="32" height="36" fill="none" stroke="#fff" stroke-width="2.5"/><path d="M8 34l9-12 6 7 4-5 7 10z" fill="#fff"/></svg>
    <h4>Posters</h4><p>Veggspjöld í öllum stærðum, tilvalin fyrir kynningar, viðburði og veggi.</p>
  </div>
  <div class="abs prod" style="left:800px;top:330px">
    <svg width="44" height="44" viewBox="0 0 44 44"><rect x="4" y="6" width="36" height="9" fill="none" stroke="#fff" stroke-width="2.5"/><rect x="7" y="17" width="32" height="9" fill="none" stroke="#fff" stroke-width="2.5"/><rect x="4" y="28" width="36" height="9" fill="none" stroke="#fff" stroke-width="2.5"/></svg>
    <h4>Textbooks</h4><p>Kennslubækur og námsefni fyrir skóla, prentað og afhent á réttum tíma.</p>
  </div>
</section>

<!-- contact -->
<h2 class="abs section-title" style="top:2380px">Contact us</h2>
<div class="abs contact-photo" role="img" aria-label="Ljósmynd af þremur brosandi nemendum með bækur"></div>
<p class="abs contact-intro">Hafðu samband og við svörum þér fljótt. Við aðstoðum með öll prentverk, stór og smá, fyrir nemendur, skóla og fyrirtæki.</p>
<div class="abs field" style="left:600px;top:2490px">Name</div>
<div class="abs field" style="left:870px;top:2490px">Email</div>
<div class="abs field" style="left:600px;top:2560px">Phone</div>
<div class="abs field" style="left:870px;top:2560px">Subject</div>
<div class="abs field" style="left:600px;top:2620px;width:520px">Message</div>
<div class="abs btn-red send">SEND NOW
  <svg width="18" height="16" viewBox="0 0 18 16"><path d="M1 8l16-7-4 14-4-5z" fill="#fff"/></svg>
</div>

<!-- footer -->
<div class="abs map" role="img" aria-label="Kort sem sýnir staðsetningu prentsmiðjunnar"></div>
<svg class="abs" style="left:300px;top:3020px" width="28" height="40" viewBox="0 0 28 40"><path d="M14 40S0 22 0 14a14 14 0 0128 0c0 8-14 26-14 26z" fill="var(--red)"/><circle cx="14" cy="14" r="5" fill="#fff"/></svg>

<footer class="abs footer">
  <h5>CONTACT US</h5><div class="line"></div>
  <div class="row" style="margin-bottom:12px">
    <svg width="14" height="18" viewBox="0 0 14 18"><path d="M7 18S0 10 0 7a7 7 0 0114 0c0 3-7 11-7 11z" fill="#cfcfcf"/></svg>
    Lindargata 12, 101 Reykjavík
  </div>
  <div class="row" style="gap:60px;margin-bottom:36px">
    <span class="row"><svg width="14" height="14" viewBox="0 0 24 24"><path d="M6 2l4 4-2 3a12 12 0 007 7l3-2 4 4-3 4C10 22 2 14 2 5z" fill="#cfcfcf"/></svg>555 0142</span>
    <span class="row"><svg width="16" height="12" viewBox="0 0 16 12"><rect x="1" y="1" width="14" height="10" fill="none" stroke="#cfcfcf" stroke-width="1.5"/><path d="M1 1l7 6 7-6" fill="none" stroke="#cfcfcf" stroke-width="1.5"/></svg>vindurgata@vindurgata.is</span>
  </div>
  <h5>OPENING HOURS</h5><div class="line"></div>
  <div class="row" style="gap:90px;margin-bottom:36px"><span>Mán – Fös: 09:00–17:00</span><span>Helgar: Lokað</span></div>
  <h5>FOLLOW US ON</h5><div class="line"></div>
  <div class="social"></div>
</footer>

<div class="abs bottom">©Vindurgata – 2018. All Rights Reserved.</div>

</body>
</html>
```